Structural Engineering Business Card

Brookvane Drafting does residential house plans for clients in Central Florida. Would like simple but elegant business card that is appropriate for a house plan engineering company. Prefer black business card with black/white them but open to other shades of blue. I uploaded a sample card that I came across that looked good but please come up with your own creative designs.

Contact Information for Business Card

Name, Title, Phone, Email, Address, website

```html
<!DOCTYPE html>
<html lang="en">
<head>
<meta charset="utf-8">
<title>Brookvane Drafting — Business Card</title>
<link href="https://fonts.googleapis.com/css2?family=Arimo:wght@400;700&display=swap" rel="stylesheet">
<style>
  :root {
    --backdrop: #b4b4b4;
    --card: #262626;
    --ink: #ffffff;
    --ink-soft: #e6e6e6;
    --radius: 26px;
  }
  * { margin: 0; padding: 0; box-sizing: border-box; }
  html, body {
    width: 1200px; height: 788px; overflow: hidden;
    background: var(--backdrop);
    font-family: "Arimo", Arial, sans-serif;
    color: var(--ink);
  }
  .sheet {
    width: 1200px; height: 788px;
    display: flex; align-items: center; justify-content: center;
    gap: 40px;
  }
  .card {
    width: 540px; height: 309px;
    background: var(--card);
    border-radius: var(--radius);
    position: relative;
    box-shadow: 0 14px 30px rgba(0,0,0,.28);
  }
  .card--contact { padding: 34px 38px; }
  .holder-name {
    font-weight: 700; font-size: 22px; letter-spacing: .5px;
    text-transform: uppercase; line-height: 1.1;
  }
  .holder-title { font-size: 17px; color: var(--ink-soft); margin-top: 2px; }
  .address {
    margin-top: 42px; font-size: 16px; line-height: 1.3; color: var(--ink-soft);
  }
  .contact-list { list-style: none; margin-top: 14px; font-size: 16px; line-height: 1.45; color: var(--ink-soft); }
  .contact-list li { display: flex; align-items: center; gap: 8px; }
  .contact-list svg { width: 13px; height: 13px; flex: none; fill: var(--ink); }
  .card--brand { display: flex; align-items: center; justify-content: center; }
  .brand-name {
    font-weight: 700; font-size: 44px; letter-spacing: 1px;
    text-transform: uppercase; color: var(--ink); text-align: center; line-height: 1.05;
  }
</style>
</head>
<body>
<main class="sheet">
  <section class="card card--contact" aria-label="Business card, contact side">
    <h1 class="holder-name">Daniel Whitcombe</h1>
    <p class="holder-title">Founder/CEO</p>
    <p class="address">2870 Harlow Ave Suite 140<br>Lakeside, FL 32810</p>
    <ul class="contact-list">
      <li>
        <svg viewBox="0 0 16 16" aria-hidden="true"><path d="M3 1h3l1.5 4-2 1.3a9 9 0 0 0 4.2 4.2L11 8.5l4 1.5v3a2 2 0 0 1-2 2C7 15 1 9 1 3a2 2 0 0 1 2-2z"/></svg>
        555.014.2280
      </li>
      <li>
        <svg viewBox="0 0 16 16" aria-hidden="true"><path d="M1 3h14v10H1z M1.5 3.5 8 9l6.5-5.5" stroke="#262626" stroke-width="1.2"/></svg>
        hello@brookvanedrafting.com
      </li>
      <li>
        <svg viewBox="0 0 16 16" aria-hidden="true"><circle cx="8" cy="8" r="7"/><path d="M1 8h14M8 1c-3 3.5-3 10.5 0 14M8 1c3 3.5 3 10.5 0 14" stroke="#262626" stroke-width="1.1" fill="none"/></svg>
        www.brookvanedrafting.com
      </li>
    </ul>
  </section>

  <section class="card card--brand" aria-label="Business card, brand side">
    <p class="brand-name">Brookvane<br>Drafting</p>
  </section>
</main>
</body>
</html>
```